Cleaning service website design

We need a new nice web design(logo will be the same) for a new cleaning service Company:

Informations about Company and logo you can take from flyers in attachments.

This is a cleaning service Company which have simple rules and we would like to show that(in checklist form) on website:

- What we do and that we're Cleaning Green

- Why us?

- How much(our pricing is simple)

Also we would like to communicate with clients by some nice/big pictures on website and the most important thing is our phone number and short/fast Brimtallow.

Also there should be some space for description about our Company.

Generally all information on main page can be short: about us, about service(what we do), last reviews, tips (for example: Tip of the week) and other can be some introduction to subpage where will be more information.

There will be few subpages like: About us, About our service, Photos(Before and after), Reviews , Tips, FAQ, Contact, Looking for a Job? - most of them will be just text so you can project just one example.

```html
<!DOCTYPE html>
<html lang="en">
<head>
<meta charset="utf-8">
<title>Tidy Nest – House Cleaning</title>
<link href="https://fonts.googleapis.com/css2?family=Open+Sans:ital,wght@0,400;0,600;0,700;1,400&family=Roboto+Condensed:wght@700&family=Yanone+Kaffeesatz:wght@400&display=swap" rel="stylesheet">
<style>
:root{
  --green:#7ab51d;
  --green-dark:#5f9416;
  --blue:#1f5fa8;
  --orange:#f07a10;
  --text:#333;
  --muted:#999;
  --line:#d9d9d9;
  --footer:#2c2c2c;
  --footer-bar:#1e1e1e;
}
*{box-sizing:border-box;margin:0;padding:0}
html,body{width:800px;height:1200px;overflow:hidden;background:#fff}
body{position:relative;font-family:"Open Sans",sans-serif;color:var(--text);font-size:9px}
.abs{position:absolute}
/* header */
.logo{left:100px;top:12px;display:flex;align-items:center;gap:6px}
.logo-dot{width:14px;height:14px;border-radius:50%;background:var(--green)}
.logo-name{font-weight:700;font-size:20px;color:var(--green)}
.call{right:100px;top:9px;text-align:right;font-size:9px}
.call b{font-weight:700}
.call .num{display:flex;align-items:center;justify-content:flex-end;gap:4px;font-size:17px;font-weight:700;color:#222;margin-top:1px}
.nav{right:100px;top:44px;display:flex;font-family:"Roboto Condensed",sans-serif;font-size:8px;text-transform:uppercase;height:44px}
.nav a{color:#222;text-decoration:none;padding:14px 9px 0}
.nav a.active{color:var(--green);background:#f2f2f2;border-bottom:4px solid var(--green)}
.nav a:last-child{padding-right:0}
.rule{left:0;top:84px;width:800px;height:4px;background:#e4e4e4}
/* hero */
.hero{left:0;top:88px;width:800px;height:336px;background:radial-gradient(ellipse at 72% 55%,#8aa84a 0%,#4f7d2c 35%,#2f5a1e 70%,#1d3d14 100%)}
.hero-title{left:100px;top:122px;color:#fff;font-size:27px;font-weight:400;letter-spacing:.5px}
.hero-title b{font-weight:700}
.hero-sub{left:100px;top:153px;color:#fff;font-size:15px;font-weight:700}
.hero-sub span{color:#e8262b;font-size:25px}
.checks{left:100px;top:190px;list-style:none;color:#fff;font-size:9.5px}
.checks li{display:flex;align-items:center;gap:8px;height:22.3px}
.cta{left:99px;top:340px;width:165px;height:39px;background:linear-gradient(#ffa62a,#f07a10);border-radius:4px;color:#fff;font-weight:700;font-size:16px;display:flex;align-items:center;justify-content:center;gap:8px}
.badge{left:283px;top:332px;width:47px;height:47px;border-radius:50%;background:radial-gradient(circle at 40% 35%,#fff,#cfe8a6 60%,#7ab51d)}
/* cards */
.card{top:450px;height:227px;border:1px solid var(--line);background:#fff;box-shadow:0 8px 8px -6px rgba(0,0,0,.15)}
.card .pic{margin:3px;height:72px}
.card h3{font-weight:400;font-size:13px;color:var(--green);text-align:center;margin:6px 0 10px}
.c1{left:99px;width:192px}.c2{left:303px;width:192px}.c3{left:507px;width:193px}
.card ul{list-style:none;padding:0 18px 0 20px;font-size:8.5px;line-height:1.45}
.card ul li{position:relative;padding-left:11px;margin-bottom:6px}
.card ul li::before{content:"";position:absolute;left:0;top:5px;width:4px;height:4px;background:#333}
.price{padding:0 22px 0 25px;font-size:8.5px;line-height:1.5}
.price p{margin-bottom:3px}
.price span{color:var(--green)}
.price a{color:var(--blue)}
.price em{display:block;font-size:7px;margin-top:20px}
.c3 h3{margin:12px 0 13px;font-size:13.5px}
.field{margin:0 20px 9px 20px;height:19px;border:1px solid #ccc;font-size:6.5px;color:var(--muted);padding:5px 7px}
.pair{display:flex;gap:10px;margin:0 20px}
.pair .field{margin:0;flex:1}
.estimate-foot{display:flex;justify-content:space-between;align-items:flex-end;margin:14px 20px 0}
.estimate-foot small{font-size:7px;font-weight:700;display:block}
.estimate-foot strong{font-size:12.5px;color:var(--blue)}
.submit{width:56px;height:18px;background:linear-gradient(#ff9a2a,#e46a08);color:#fff;font-size:8px;font-weight:700;display:flex;align-items:center;justify-content:center}
/* about */
.about{left:99px;top:707px;width:601px;height:94px;border:1px solid var(--line);background:#f7f7f7}
.about .pic{position:absolute;left:2px;bottom:0;width:148px;height:90px}
.about h2{position:absolute;left:156px;top:14px;font-family:"Yanone Kaffeesatz",sans-serif;font-weight:400;font-size:22px;color:var(--green)}
.about p{position:absolute;left:156px;top:41px;width:432px;font-size:8px;line-height:1.55}
.about .more{position:absolute;right:12px;top:68px;font-size:6.5px;color:var(--green)}
/* reviews */
.lower{left:99px;top:828px;width:601px;height:164px;border:1px solid var(--line)}
.lower h2{position:absolute;font-weight:400;font-size:13.5px;color:var(--green)}
.rev-pic{position:absolute;left:13px;top:61px;width:90px;height:102px}
.bubble{position:absolute;left:88px;top:36px;width:236px;height:67px;border:1px solid var(--line);border-radius:3px;padding:8px 10px;background:#fff}
.bubble .who{font-size:7.5px;font-weight:700}
.bubble .who span{font-weight:400;color:var(--muted);margin-left:12px}
.bubble i{display:block;font-size:8px;line-height:1.5;color:#555;margin-top:4px}
.bubble .meta{border-top:1px dotted #bbb;margin-top:3px;padding-top:3px;font-size:6.5px;display:flex;gap:8px}
.bubble .meta a{color:var(--blue)}
.stars{color:#e0262b;letter-spacing:-1px}
.more-btn{position:absolute;width:61px;height:16px;background:var(--green);color:#fff;font-size:7.5px;display:flex;align-items:center;justify-content:center}
.divider{position:absolute;left:361px;top:44px;width:1px;height:96px;background:var(--line)}
.tip-link{position:absolute;left:384px;top:44px;font-size:9px;font-weight:600;color:var(--blue);text-decoration:underline}
.tip-text{position:absolute;left:384px;top:64px;width:200px;font-size:8px;line-height:1.55}
/* footer */
.footer{left:0;top:1017px;width:800px;height:156px;background:var(--footer);color:#fff}
.fcol{position:absolute;top:27px}
.fcol h4{font-size:10.5px;font-weight:600;margin-bottom:8px}
.fcol ul{list-style:none;font-size:7.5px;line-height:15.5px}
.fcol p{font-size:7.5px;margin-bottom:8px}
.email{display:flex;gap:3px}
.email div{width:202px;height:27px;background:#fff;color:#222;font-size:7.5px;padding:9px 10px;border-radius:2px}
.email b{width:28px;height:27px;background:#f5a20f;border-radius:2px;display:flex;align-items:center;justify-content:center;font-size:9px}
.socials{position:absolute;left:464px;top:122px;display:flex;gap:5px}
.socials span{width:15px;height:15px;border-radius:2px}
.flogo{position:absolute;right:100px;top:117px;display:flex;align-items:center;gap:5px}
.flogo .logo-name{font-size:14px}
.bar{left:0;top:1173px;width:800px;height:27px;background:var(--footer-bar);color:#555;font-size:7.5px;padding:9px 100px}
</style>
</head>
<body>
<header>
  <div class="abs logo"><span class="logo-dot"></span><span class="logo-name">Tidy Nest</span></div>
  <div class="abs call"><b>Call Us</b> to arrange your cleaning on
    <div class="num"><svg width="11" height="13" viewBox="0 0 24 24"><path fill="#1f5fa8" d="M6.6 10.8a15 15 0 0 0 6.6 6.6l2.2-2.2a1 1 0 0 1 1-.25 11.4 11.4 0 0 0 3.6.57 1 1 0 0 1 1 1V20a1 1 0 0 1-1 1A17 17 0 0 1 3 4a1 1 0 0 1 1-1h3.5a1 1 0 0 1 1 1c0 1.25.2 2.45.57 3.57a1 1 0 0 1-.25 1z"/></svg>555-014-2290</div>
  </div>
  <nav class="abs nav">
    <a class="active">Home</a><a>About Us</a><a>Our Services</a><a>Photos</a><a>Reviews</a><a>Tips</a><a>Careers</a><a>FAQ</a><a>Contact</a>
  </nav>
  <div class="abs rule"></div>
</header>

<section>
  <div class="abs hero" role="img" aria-label="Photo of a woman in a green dress stretching her arms in a lush green forest"></div>
  <h1 class="abs hero-title">SIMPLIFY <b>YOUR LIFE</b></h1>
  <p class="abs hero-sub">and some there House Cleaning from <span>$79</span></p>
  <ul class="abs checks">
    <li><svg width="12" height="12" viewBox="0 0 12 12"><path d="M1 11C1 5 5 1 11 1 11 7 7 11 1 11z" fill="#8cc63f"/></svg>Locally Owned &amp; Operated</li>
    <li><svg width="12" height="12" viewBox="0 0 12 12"><path d="M1 11C1 5 5 1 11 1 11 7 7 11 1 11z" fill="#8cc63f"/></svg>Reliable &amp; Affordable</li>
    <li><svg width="12" height="12" viewBox="0 0 12 12"><path d="M1 11C1 5 5 1 11 1 11 7 7 11 1 11z" fill="#8cc63f"/></svg>All Supplies Provided</li>
    <li><svg width="12" height="12" viewBox="0 0 12 12"><path d="M1 11C1 5 5 1 11 1 11 7 7 11 1 11z" fill="#8cc63f"/></svg>No Contracts</li>
    <li><svg width="12" height="12" viewBox="0 0 12 12"><path d="M1 11C1 5 5 1 11 1 11 7 7 11 1 11z" fill="#8cc63f"/></svg>Pet Friendly</li>
    <li><svg width="12" height="12" viewBox="0 0 12 12"><path d="M1 11C1 5 5 1 11 1 11 7 7 11 1 11z" fill="#8cc63f"/></svg>Green Cleaning</li>
  </ul>
  <div class="abs cta">GET STARTED <svg width="18" height="14" viewBox="0 0 18 14"><path d="M0 4h9V0l9 7-9 7v-4H0z" fill="#fff"/></svg></div>
  <div class="abs badge"></div>
</section>

<section>
  <div class="abs card c1">
    <div class="pic" style="background:linear-gradient(90deg,#b59a78,#e8d7c0,#a88b66)" role="img" aria-label="Photo of a smiling family with a dog on a sofa"></div>
    <h3>What do we clean?</h3>
    <ul>
      <li>Thoroughly clean your bathrooms, kitchen, bedrooms and living areas</li>
      <li>Mop or vacuum your floors</li>
      <li>Dust surfaces</li>
      <li>Collect garbage</li>
      <li>Make beds</li>
    </ul>
  </div>
  <div class="abs card c2">
    <div class="pic" style="background:linear-gradient(90deg,#c9b8a2,#e9dfd2,#8fa0b5)" role="img" aria-label="Photo of a family looking at a laptop together"></div>
    <h3>Pricing is..simple</h3>
    <div class="price">
      <p><span>$79</span> for homes less than 1000 sq ft</p>
      <p><span>$89</span> for homes 1000-1800 sq ft</p>
      <p><span>$99</span> for homes 1800-2600 sq ft</p>
      <p>If your home is larger than 2600 sq ft please <a>call for a quote</a></p>
      <em>*rates are for regular service*</em>
    </div>
  </div>
  <div class="abs card c3">
    <h3>Quick Brimtallow</h3>
    <div class="field">Name</div>
    <div class="field">E-mail</div>
    <div class="field">Postal Code</div>
    <div class="field">Phone</div>
    <div class="pair"><div class="field">No. of Bathrooms</div><div class="field">No. of Bedrooms</div></div>
    <div class="estimate-foot">
      <div><small>CALL US TODAY</small><strong>555-014-2290</strong></div>
      <div class="submit">SUBMIT</div>
    </div>
  </div>
</section>

<section class="abs about">
  <div class="pic" style="background:linear-gradient(90deg,#3a3f4a,#c7a98c,#5a5148)" role="img" aria-label="Photo of the company owners, a man and a woman"></div>
  <h2>About Tidy Nest</h2>
  <p>It’s about caring, not just cleaning. Having personally experienced the struggles of finding quality maid service for our home, we want to make it simpler for families in the Riverton area. Our goal is to provide caring, consistent and reliable house cleaning to every customer we serve.</p>
  <span class="more">READ MORE...</span>
</section>

<section class="abs lower">
  <h2 style="left:18px;top:14px">Featured Review</h2>
  <div class="rev-pic" style="background:linear-gradient(#e6d2b8,#2b2b30)" role="img" aria-label="Photo of a smiling businesswoman"></div>
  <div class="bubble">
    <div class="who">Dana Morrow, Riverton<span>1 review</span></div>
    <i>I had to move out of a rental property and didn't want to hassle with the cleaning, so I called Tidy Nest whom quoted me over the phone and did a brilliant job.</i>
    <div class="meta"><span class="stars">★★★★★</span><span>09/07/2013</span><a>COMMENT</a><a>REPORT</a><a>Share</a><span>HELPFUL?</span></div>
  </div>
  <div class="more-btn" style="left:261px;top:137px">View more &gt;</div>
  <div class="divider"></div>
  <h2 style="left:384px;top:14px">Tip of the Week</h2>
  <a class="tip-link">Cleaning up after your dog or cat</a>
  <p class="tip-text">For millions of dog and cat owners, Fido and Fluffy aren’t just pets – they’re part of the family.<br>But as much as we love our four-legged friends, they sure can .....</p>
  <div class="more-btn" style="left:513px;top:137px">View more &gt;</div>
</section>

<footer class="abs footer">
  <div class="fcol" style="left:100px"><h4>Quick Links</h4><ul><li>Home</li><li>About Us</li><li>Our Service</li><li>Photos</li><li>Contact</li></ul></div>
  <div class="fcol" style="left:220px"><h4>Useful Links</h4><ul><li>Terms of use</li><li>Privacy Policy</li><li>Help Center</li><li>Community</li><li>Login Area</li></ul></div>
  <div class="fcol" style="left:328px"><h4>Join Our Community</h4><ul><li>Friendbook</li><li>Chirpline</li><li>Worknet</li></ul></div>
  <div class="fcol" style="left:464px"><h4>SignUp For Our Monthly Newsletter</h4><p>Subscribe our newsletter &amp; get the latest news &amp; updates</p>
    <div class="email"><div>Email Address</div><b>GO</b></div></div>
  <div class="socials"><span style="background:#3b5998"></span><span style="background:#39a9e0"></span><span style="background:#f2a31b"></span></div>
  <div class="flogo"><span class="logo-dot"></span><span class="logo-name">Tidy Nest</span></div>
</footer>
<div class="abs bar">© 2013 by, Tidy Nest. All Rights Reserved.</div>
</body>
</html>
```